Business cards in digital learning for freelancer

Hello, I need a business cards in french. I work in the Digital learning industries as freeelancer; I'm an expert in digital learning. I work in France. My customer are in the health industry, pharmaceutical industry, and training organization. I've got a logo. I offer three services: consulting, Design, and Training. In the consulting, I offers coaching to choose your digital learning tools and the digital learning strategy. For the Design, I product differents level of elearning like rapid-learning, elearning, micro-learning, video-learning. And for the training service, I've create training about pedagogy, digital learning management project, Digital learning design.
I join my Logo create in this platform. My universe is gamified. I like the life, and I'm very social. I want a card like I'm I. I love Art (painting), Europeen comics. I use in my visual support "permanent maker" font and caracters. I would like cards: elegant, modern, Top class. If you need any information, you can ask me.
thanks for ideas

Target Market(s)

in health industries and training organization for Training manager, instructor, human resources director

Contact Information for Business Card

Phone number : 06 71 38 95 14 , mail: bastiengolmier@quelmoto.fr, web: bastiengolmier.fr , Carrivo

Font styles to use
Sans Serif

Requirements
Must have
• Use my logo and write my 3 services (consulting, training, design)

```html
<!DOCTYPE html>
<html lang="fr">
<head>
<meta charset="utf-8">
<title>Golmier – Cartes de visite</title>
<link rel="stylesheet" href="https://fonts.googleapis.com/css2?family=Cinzel:wght@400&family=Roboto:wght@400;700&display=swap">
<style>
  :root {
    --orange: #f37323;
    --grey: #707070;
    --grey-text: #5a5a5a;
    --line: #8a8a8a;
    --paper: #ffffff;
    --backdrop: #a3a3a3;
  }
  * { margin: 0; padding: 0; box-sizing: border-box; }
  html, body { width: 1200px; height: 1200px; overflow: hidden; }
  body { background: var(--backdrop); position: relative; font-family: "Roboto", Arial, sans-serif; }

  .card { position: absolute; top: 303px; width: 368px; height: 594px; background: var(--paper); }
  .card--back { left: 200px; overflow: hidden; }
  .card--front { left: 599px; }

  .brand-pattern {
    position: absolute; inset: 0;
    background: linear-gradient(100deg, var(--grey) 0%, var(--grey) 30%, #f4f4f4 45%, #f4f4f4 55%, var(--orange) 70%, var(--orange) 100%);
  }

  .centered { position: absolute; left: 0; width: 100%; text-align: center; }

  .brand-mark {
    position: absolute; top: 76px; left: 129px;
    width: 110px; height: 110px; border-radius: 50%;
    background: var(--orange);
  }

  .wordmark {
    top: 204px; font-weight: 700; font-size: 38px; letter-spacing: 7px;
    color: var(--orange); line-height: 1; padding-left: 7px;
  }
  .tagline {
    top: 238px; display: flex; align-items: center; justify-content: center; gap: 8px;
    font-family: "Cinzel", Georgia, serif; font-size: 13px; color: var(--grey-text); letter-spacing: 1px;
  }
  .tagline::before, .tagline::after { content: ""; width: 52px; height: 1px; background: var(--grey-text); }

  .services {
    top: 271px; font-size: 15.5px; color: var(--grey-text); letter-spacing: 0.3px;
    display: flex; justify-content: center; align-items: center; gap: 8px;
  }
  .services .dot { width: 8px; height: 8px; border-radius: 50%; background: var(--orange); }

  .person-name {
    top: 370px; font-family: "Cinzel", Georgia, serif; font-size: 23px; color: var(--orange); letter-spacing: 0.5px;
  }
  .person-role { top: 398px; font-size: 16px; color: var(--grey-text); }

  .contact-icons {
    top: 430px; display: flex; justify-content: center; align-items: center; gap: 4px;
  }
  .contact-icons .rule { width: 52px; height: 1px; background: var(--line); margin: 0 4px; }
  .icon-box {
    width: 25px; height: 25px; border-radius: 3px; background: var(--orange);
    display: flex; align-items: center; justify-content: center;
  }

  .contact-lines { top: 466px; font-size: 16.5px; color: var(--grey-text); line-height: 21.5px; }

  .social {
    top: 543px; display: flex; justify-content: center; align-items: center; gap: 7px;
    font-size: 14px; color: var(--grey-text);
  }
  .social .rule { width: 62px; height: 1px; background: var(--line); margin: 0 4px; }
  .social .mark { width: 12px; height: 12px; border-radius: 50%; background: var(--orange); }
</style>
</head>
<body>

  <section class="card card--back">
    <div class="brand-pattern" role="img" aria-label="Large brand emblem decoration in grey, white and orange"></div>
  </section>

  <section class="card card--front">
    <div class="brand-mark" role="img" aria-label="Golmier brand emblem"></div>
    <div class="centered wordmark">GOLMIER</div>
    <div class="centered tagline">Digital Learning</div>
    <div class="centered services">
      <span>CONSULTING</span><span class="dot"></span><span>TRAINING</span><span class="dot"></span><span>DESIGN</span>
    </div>

    <div class="centered person-name">BASTIEN GOLMIER</div>
    <div class="centered person-role">Managing Director</div>

    <div class="centered contact-icons">
      <span class="rule"></span>
      <span class="icon-box" aria-label="Téléphone">
        <svg width="15" height="15" viewBox="0 0 16 16"><path fill="#fff" d="M2 6c0-2 2-3 6-3s6 1 6 3v1h-3V5.5H5V7H2zM4 8h8l1.5 5h-11z"/></svg>
      </span>
      <span class="icon-box" aria-label="E-mail">
        <svg width="15" height="15" viewBox="0 0 16 16"><rect x="1.5" y="3.5" width="13" height="9" fill="none" stroke="#fff" stroke-width="1.3"/><path d="M1.5 3.5 8 9l6.5-5.5" fill="none" stroke="#fff" stroke-width="1.3"/></svg>
      </span>
      <span class="icon-box" aria-label="Site web">
        <svg width="15" height="15" viewBox="0 0 16 16"><circle cx="8" cy="8" r="6.5" fill="#fff"/><circle cx="6.5" cy="6.5" r="2.5" fill="#f37323"/><circle cx="10.5" cy="11" r="1.5" fill="#f37323"/></svg>
      </span>
      <span class="rule"></span>
    </div>

    <div class="centered contact-lines">
      <p>06 71 38 95 14</p>
      <p>bastiengolmier@quelmoto.fr</p>
      <p>www.bastiengolmier.fr</p>
    </div>

    <div class="centered social">
      <span class="rule"></span>
      <span class="mark"></span><span>Carrivo</span>
      <span class="rule"></span>
    </div>
  </section>

</body>
</html>
```